Natural Medicine & Health/Fitness Coaching studio requires web page

Require a innovative web page for a studio that coaches clients to better health, nutrition and fitness. The studio compromises of Clinical Nutritionists, Naturopaths, Rehab Trainers, Personal Trainers and Sport Coaches. Would like to see earthy but bold designs emphasizing nutritional health and athletic performance.
Updates

Design only launched today.

Target Market(s)

All genders from 20's to 60's, as well as families

Industry/Entity Type

Nutritionist

Coding

Coded - Design and coding required

Number of Pages Required

3 page

Colors
abd037
3277b5
fbee3d
fece3e
33b8a4
f04a50

Requirements
Must have
• Online booking system, ability to message
• Home page
• Coaching/Fitness page
• Nutritional Medicine page
• Must be suitable for both Fitness and Nutrition

```html
<!DOCTYPE html>
<html lang="en">
<head>
<meta charset="utf-8">
<title>Evergreen Vitality – Nutrition &amp; Fitness Therapy</title>
<link rel="stylesheet" href="https://fonts.googleapis.com/css2?family=Poppins:wght@400;500;600;700;800&family=Open+Sans:wght@400;600&display=swap">
<style>
:root{
  --green:#abd037;
  --green-dark:#8fbb22;
  --blue:#3277b5;
  --navy:#1d4f86;
  --yellow:#fece3e;
  --teal:#33b8a4;
  --red:#f04a50;
  --ink:#222;
  --muted:#777;
  --white:#fff;
}
*{box-sizing:border-box;margin:0;padding:0}
html,body{width:1200px;height:3681px;overflow:hidden}
body{position:relative;background:var(--white);font-family:"Open Sans",Arial,sans-serif;color:var(--ink)}
.abs{position:absolute}

/* header */
.site-header{left:0;top:0;width:1200px;height:103px;background:var(--white)}
.brand{left:162px;top:37px;font-family:"Poppins",Arial,sans-serif;font-weight:600;font-size:22px;line-height:30px;color:var(--green-dark);display:flex;align-items:center;gap:8px;white-space:nowrap}
.brand-dot{width:13px;height:13px;border-radius:50%;background:var(--navy);flex:none}
.main-nav a{position:absolute;top:40px;font-family:"Poppins",Arial,sans-serif;font-size:17px;color:var(--navy);text-decoration:none;white-space:nowrap}
.main-nav a.active{top:32px;left:459px;width:86px;height:42px;border-radius:21px;background:var(--navy);color:var(--white);display:flex;align-items:center;justify-content:center}

/* hero */
.hero{left:0;top:103px;width:1200px;height:580px;background:linear-gradient(120deg,#3a3d40 0%,#6e7174 45%,#4b4e51 70%,#2e3134 100%)}
.hero-title{left:0;top:294px;width:1200px;text-align:center;font-family:"Poppins",Arial,sans-serif;font-weight:700;font-size:45px;color:var(--white);letter-spacing:.3px}
.hero-sub{left:0;top:352px;width:1200px;text-align:center;font-family:"Poppins",Arial,sans-serif;font-weight:600;font-size:24px;color:var(--white)}
.btn-book{left:510px;top:407px;width:175px;height:52px;border-radius:26px;background:var(--green);color:var(--white);font-family:"Poppins",Arial,sans-serif;font-weight:600;font-size:19px;display:flex;align-items:center;justify-content:center}
.dots{left:566px;top:588px;display:flex;gap:10px}
.dots span{width:13px;height:13px;border-radius:50%;border:2px solid var(--white)}
.dots span.on{background:var(--white)}

/* about */
.about-bg{left:0;top:630px;width:1200px;height:470px}
.about-title{left:0;top:714px;width:1200px;text-align:center;font-family:"Poppins",Arial,sans-serif;font-weight:700;font-size:29px;color:var(--white)}
.about-text{left:275px;width:650px;text-align:center;color:var(--white);font-size:16px;line-height:26px}
.btn-outline{border:2px solid var(--white);border-radius:27px;color:var(--white);font-family:"Poppins",Arial,sans-serif;font-weight:600;font-size:18px;display:flex;align-items:center;justify-content:center}

/* services */
.section-title{left:0;width:1200px;text-align:center;font-family:"Poppins",Arial,sans-serif;font-weight:700;font-size:30px;color:var(--navy)}
.service-card{padding:40px 38px;color:var(--white)}
.service-card h3{font-family:"Poppins",Arial,sans-serif;font-weight:600;font-size:28px;margin-bottom:8px}
.service-card p{font-size:15.5px;line-height:23px}
.service-card .btn-outline{width:140px;height:44px;font-size:15px;margin-top:18px;border-radius:22px}
.card-line{width:7px}

/* booking */
.booking-bg{left:0;top:2495px;width:1200px;height:560px}
.booking-title{left:0;top:2634px;width:1200px;text-align:center;font-family:"Poppins",Arial,sans-serif;font-weight:600;font-size:29px;color:var(--white)}
.field{background:var(--white);border:1px solid #ddd;font-size:16px;color:#555;padding:12px 20px}
.btn-submit{left:513px;top:2935px;width:172px;height:45px;border-radius:23px;background:var(--red);color:var(--white);font-family:"Poppins",Arial,sans-serif;font-weight:500;font-size:18px;display:flex;align-items:center;justify-content:center}

/* blogs */
.blogs-title{left:174px;top:3120px;font-family:"Poppins",Arial,sans-serif;font-weight:700;font-size:29px;color:var(--navy)}
.blog-card{top:3183px;width:270px}
.blog-img{width:270px;height:167px;position:relative}
.blog-date{position:absolute;left:0;bottom:0;background:var(--teal);color:var(--white);font-size:13px;padding:5px 24px}
.blog-card h4{font-family:"Open Sans",Arial,sans-serif;font-weight:600;font-size:14px;line-height:18px;margin-top:14px;color:var(--ink)}
.blog-card p{font-size:10.5px;line-height:14px;color:var(--muted);margin-top:8px}
.blog-card .read{display:block;margin-top:8px;font-size:13px;color:var(--red);font-weight:600}

/* footer */
.site-footer{left:0;top:3541px;width:1200px;height:140px;background:var(--green)}
.footer-nav{left:190px;top:3574px;display:flex;gap:22px;font-family:"Poppins",Arial,sans-serif;font-weight:600;font-size:16px;color:var(--white)}
.copyright{left:190px;top:3613px;font-size:12px;color:var(--white)}
.social{top:3578px;width:30px;height:30px;border-radius:50%;border:2px solid var(--white)}
</style>
</head>
<body>

<header class="site-header abs">
  <div class="brand abs"><span class="brand-dot"></span>Evergreen Vitality</div>
  <nav class="main-nav">
    <a class="active" href="#">Home</a>
    <a href="#" style="left:562px">About us</a>
    <a href="#" style="left:657px">Coaching</a>
    <a href="#" style="left:760px">Fitness</a>
    <a href="#" style="left:839px">Nutrition</a>
    <a href="#" style="left:931px">Contact us</a>
  </nav>
</header>

<section class="hero abs" role="img" aria-label="Photo of a woman stretching in a gym beside large windows"></section>
<h1 class="hero-title abs">NUTRITION &amp; FITNESS THERAPY</h1>
<div class="hero-sub abs">PELLENTESQUE FAUCIBUS ACCUMSAN ULTRICIES</div>
<div class="btn-book abs">Book Now</div>
<div class="dots abs"><span></span><span class="on"></span><span></span></div>

<svg class="about-bg abs" viewBox="0 0 1200 470" role="img" aria-label="Blue band over a faint photo of berries">
  <defs>
    <linearGradient id="aboutGrad" x1="0" y1="0" x2="1" y2="1">
      <stop offset="0" stop-color="#1f4f96"/>
      <stop offset="0.5" stop-color="#2a60ad"/>
      <stop offset="1" stop-color="#1c4b8e"/>
    </linearGradient>
  </defs>
  <path d="M0 362 Q600 470 1200 362 L1200 388 Q600 480 0 388 Z" fill="#abd037"/>
  <path d="M0 40 Q600 20 1200 40 L1200 362 Q600 460 0 362 Z" fill="url(#aboutGrad)"/>
</svg>
<h2 class="about-title abs">ABOUT EVERGREEN VITALITY</h2>
<p class="about-text abs" style="top:776px">Pellentesque faucibus Ut accumsan ultricies elit Maecenas at justo id velit placerat molestie Donec dictum lectus non odio Cras a ante vitae enim</p>
<p class="about-text abs" style="top:840px">Aaculis aliquam Mauris nunc quam venenatis nec euismod sit amet egestas placerat est Pellentesque habitant morbi tristique senectus et netus et malesuada fames ac turpis egestas Cras id elit Integer quis urna Ut ante enim</p>
<div class="btn-outline abs" style="left:511px;top:950px;width:180px;height:54px">Read More</div>

<h2 class="section-title abs" style="top:1168px">WHAT WE DO</h2>

<div class="abs" style="left:162px;top:1256px;width:584px;height:366px;background:linear-gradient(135deg,#d9d4cf,#b9b2ab 50%,#8e8985)" role="img" aria-label="Photo of a trainer guiding a woman on an exercise ball"></div>
<div class="service-card abs" style="left:626px;top:1288px;width:415px;height:300px;background:var(--yellow)">
  <h3>Coaching</h3>
  <p>Mauris vel lacus vitae felis vestibulum volutpat Etiam est nunc venenatis in tristique eu imperdiet ac nisl Cum sociis natoque penatibus et magnis dis parturient montes nascetur ridiculus mus in iaculis</p>
  <div class="btn-outline">Read More</div>
</div>
<div class="card-line abs" style="left:1043px;top:1288px;height:300px;background:var(--yellow)"></div>

<div class="abs" style="left:444px;top:1688px;width:584px;height:368px;background:linear-gradient(135deg,#6b6661,#a79f97 45%,#4d4a47)" role="img" aria-label="Photo of two women giving a high five during a gym workout"></div>
<div class="service-card abs" style="left:154px;top:1718px;width:415px;height:294px;background:var(--blue)">
  <h3>Fitness</h3>
  <p>Mauris vel lacus vitae felis vestibulum volutpat Etiam est nunc venenatis in tristique eu imperdiet ac nisl Cum sociis natoque penatibus et magnis dis parturient montes nascetur ridiculus mus in iaculis</p>
  <div class="btn-outline">Read More</div>
</div>
<div class="card-line abs" style="left:144px;top:1718px;height:294px;background:var(--blue)"></div>

<div class="abs" style="left:177px;top:2110px;width:586px;height:368px;background:linear-gradient(135deg,#8a6a4a,#5d6b3a 45%,#6e4a30 75%,#a13a2e)" role="img" aria-label="Photo of beans, berries, nuts, salmon, olive oil and tomatoes on wood"></div>
<div class="service-card abs" style="left:643px;top:2147px;width:411px;height:295px;background:var(--red)">
  <h3>Nutrition</h3>
  <p>Mauris vel lacus vitae felis vestibulum volutpat Etiam est nunc venenatis in tristique eu imperdiet ac nisl Cum sociis natoque penatibus et magnis dis parturient montes nascetur ridiculus mus in iaculis</p>
  <div class="btn-outline">Read More</div>
</div>
<div class="card-line abs" style="left:1056px;top:2147px;height:295px;background:var(--red)"></div>

<svg class="booking-bg abs" viewBox="0 0 1200 560" role="img" aria-label="Teal to green band over a faint photo of a smiling woman">
  <defs>
    <linearGradient id="bookGrad" x1="0" y1="0" x2="1" y2="0.4">
      <stop offset="0" stop-color="#33b8a4"/>
      <stop offset="0.55" stop-color="#6fc46a"/>
      <stop offset="1" stop-color="#abd037"/>
    </linearGradient>
  </defs>
  <path d="M0 8 Q600 130 1200 40 L1200 560 L0 560 Z" fill="url(#bookGrad)"/>
</svg>
<h2 class="booking-title abs">ONLINE BOOKING</h2>
<div class="field abs" style="left:177px;top:2699px;width:407px;height:47px">Your Name</div>
<div class="field abs" style="left:599px;top:2699px;width:405px;height:47px">Phone</div>
<div class="field abs" style="left:177px;top:2758px;width:407px;height:47px">Email</div>
<div class="field abs" style="left:599px;top:2758px;width:405px;height:47px">City</div>
<div class="field abs" style="left:177px;top:2822px;width:827px;height:84px">Message</div>
<div class="btn-submit abs">Submit</div>

<h2 class="blogs-title abs">OUR BLOGS</h2>
<article class="blog-card abs" style="left:177px">
  <div class="blog-img" style="background:linear-gradient(135deg,#b8aa9c,#7d7268)" role="img" aria-label="Photo of a couple exercising in a gym"><span class="blog-date">02 May 2018</span></div>
  <h4>Praesent elementum elit at tellus nec ultricies sit amet porttito</h4>
  <p>netus et malesuada fames ac turpis egestas Cras id elit Integer quis urna Ut ante enim dapibus malesuada</p>
  <span class="read">READ MORE</span>
</article>
<article class="blog-card abs" style="left:471px">
  <div class="blog-img" style="background:linear-gradient(135deg,#2fc2e0,#e9633a 60%,#f2b62f)" role="img" aria-label="Photo of sliced citrus, mango and pomegranate on a blue background"><span class="blog-date">02 May 2018</span></div>
  <h4>Nunc tempus felis vitae urna Vivamus porttitor neque at</h4>
  <p>netus et malesuada fames ac turpis egestas Cras id elit Integer quis urna Ut ante enim dapibus malesuada</p>
  <span class="read">READ MORE</span>
</article>
<article class="blog-card abs" style="left:766px">
  <div class="blog-img" style="background:linear-gradient(135deg,#f1ece6,#d9a58a 55%,#c4445a)" role="img" aria-label="Photo of a woman in sportswear holding an apple"><span class="blog-date">02 May 2018</span></div>
  <h4>Morbi porta libero id ullamcorper nonummy nibh ligula pulvina</h4>
  <p>netus et malesuada fames ac turpis egestas Cras id elit Integer quis urna Ut ante enim dapibus malesuada</p>
  <span class="read">READ MORE</span>
</article>

<footer class="site-footer abs"></footer>
<nav class="footer-nav abs"><span>Home</span><span>About us</span><span>Coaching</span><span>Fitness</span><span>Nutrition</span><span>Contact us</span></nav>
<div class="copyright abs">© 2018 Company Name. All right reserved.</div>
<span class="social abs" style="left:930px"></span>
<span class="social abs" style="left:967px"></span>
<span class="social abs" style="left:1004px"></span>

</body>
</html>
```